NZ First of it's kind solutions directory and marketplace for busy Mums needs a business card design

We need a business card design for our new nationwide business in NZ (long term plans to go global). We provide solutions to the everyday challenges that busy Mums face by connecting them with quality communities and suppliers of carefully selected, relevant products and services. We sell direct via our online marketplace. The final design should communicate our values of inclusivity, quality and smart solutions. Colours should incorporate our logo colour palette of #477077 and #6ba8b2. Our website is at https://www.brightnestmums.example

Target Market(s)

busy Mums, Age 28 – 50, female, income over $100K, location main centres NZ primarily but NZ wide. Is likely juggling work or career with a young family. Probably had hobbies which have fallen by the wayside.
-Wants to succeed in her chosen career without compromising on family life
-to successfully juggle her career without feeling like she is compromising her children
- Is time poor, something always has to give and it’s generally her health (she’ll stay up late, get stressed)
- probably ex corporate or professional career. Has discretional income

Industry/Entity Type

Business

Contact Information for Business Card

Lena Forbisher, Founder, BrightNestMums.example (Strapline Tap; Gather; Sorted), 47 Kowhai Terrace, Ellerslie, Auckland 1051, New Zealand. Mob: 021 483 517 Ph: +64 (0)9 571 4860

Font styles to use
Other font styles liked:
• Raleway, and/or Architects Daughter

Colors
00a990
33b8a4
86cfc6
cfeae6

Requirements
Must have
• the above details, streamline. the logo and colours associated with those logos
Should not have
• foil or metallic colours

```html
<!DOCTYPE html>
<html lang="en">
<head>
<meta charset="utf-8">
<title>BrightNestMums — Business Card</title>
<link href="https://fonts.googleapis.com/css2?family=Roboto:wght@400;700&family=Roboto+Condensed:wght@400&display=swap" rel="stylesheet">
<style>
  :root {
    --backdrop: #2b2b2b;
    --teal-dark: #477077;
    --teal-deep: #3f6369;
    --teal-light: #6ba8b2;
    --paper: #f1f1f1;
    --white: #ffffff;
  }
  * { margin: 0; padding: 0; box-sizing: border-box; }
  html, body {
    width: 1200px; height: 960px; overflow: hidden;
    background: var(--backdrop);
    font-family: "Roboto", Arial, sans-serif;
  }
  .canvas { position: relative; width: 1200px; height: 960px; }

  .card {
    position: absolute;
    width: 600px; height: 343px;
    border-radius: 20px;
    overflow: hidden;
  }
  .card--front { left: 314px; top: 113px; background: linear-gradient(160deg, var(--teal-dark), var(--teal-deep)); }
  .card--back { left: 311px; top: 472px; background: var(--teal-light); }

  .front-curve { position: absolute; inset: 0; }

  .holder { position: absolute; left: 43px; top: 48px; }
  .holder__name {
    font-family: "Roboto Condensed", "Arial Narrow", sans-serif;
    font-size: 21px; color: var(--teal-light); letter-spacing: 0.2px;
    line-height: 1.1;
  }
  .holder__role { font-size: 15px; color: var(--white); margin-top: 3px; }

  .address {
    position: absolute; left: 43px; top: 197px;
    font-size: 14.5px; line-height: 19px; color: var(--white);
  }
  .contacts {
    position: absolute; left: 43px; top: 244px;
    list-style: none; font-size: 14.5px; line-height: 19px; color: var(--white);
  }
  .contacts li { display: flex; align-items: center; gap: 8px; }
  .contacts svg { width: 13px; height: 13px; flex: none; }

  .brand {
    position: absolute; display: flex; align-items: center;
    font-weight: 700; color: var(--teal-dark); letter-spacing: -0.5px;
  }
  .brand__dot { border-radius: 50%; background: var(--teal-dark); flex: none; }
  .brand--front { left: 326px; top: 92px; font-size: 27px; gap: 10px; }
  .brand--front .brand__dot { width: 24px; height: 24px; }
  .brand--back { left: 0; right: 0; justify-content: center; top: 148px; font-size: 40px; gap: 14px; }
  .brand--back .brand__dot { width: 36px; height: 36px; }

  .strapline {
    position: absolute; left: 0; right: 0; top: 285px;
    text-align: center; font-size: 14.5px; color: var(--white);
  }
</style>
</head>
<body>
<main class="canvas">
  <section class="card card--front" aria-label="Card front">
    <svg class="front-curve" viewBox="0 0 600 343" width="600" height="343" aria-hidden="true">
      <path d="M348 0 C238 30 228 190 384 343 L600 343 L600 0 Z" fill="var(--teal-light)"/>
      <path d="M392 0 C262 20 256 200 390 343 L600 343 L600 0 Z" fill="var(--paper)"/>
      <path d="M372 1 C250 28 240 196 386 343" fill="none" stroke="var(--white)" stroke-width="2"/>
    </svg>

    <div class="holder">
      <p class="holder__name">LENA FORBISHER</p>
      <p class="holder__role">FOUNDER</p>
    </div>

    <address class="address" style="font-style:normal">
      47 Kowhai Terrace, Ellerslie<br>
      Auckland 1051, New Zealand.
    </address>

    <ul class="contacts">
      <li>
        <svg viewBox="0 0 16 16" aria-hidden="true"><path d="M3.5 1 L6 1 L7 5 L5.3 6.3 C6.2 8.2 7.8 9.8 9.7 10.7 L11 9 L15 10 L15 12.5 C15 13.9 13.9 15 12.5 15 C6.2 15 1 9.8 1 3.5 C1 2.1 2.1 1 3.5 1 Z" fill="var(--teal-light)"/></svg>
        <span>+64 (0)9 571 4860</span>
      </li>
      <li>
        <svg viewBox="0 0 16 16" aria-hidden="true"><rect x="4" y="0.5" width="8" height="15" rx="1.5" fill="var(--teal-light)"/><rect x="5.3" y="2.3" width="5.4" height="9.5" fill="var(--teal-dark)"/></svg>
        <span>021 483 517</span>
      </li>
      <li>
        <svg viewBox="0 0 16 16" aria-hidden="true"><circle cx="8" cy="8" r="7" fill="var(--teal-light)"/><path d="M4 5 C6 4 7 6 6 8 C5 10 7 11 7 13 M10 3 C9 5 11 6 12 7 C13 9 11 10 11 12" stroke="var(--teal-dark)" stroke-width="1.3" fill="none"/></svg>
        <span>BrightNestMums.example</span>
      </li>
    </ul>

    <div class="brand brand--front">
      <span class="brand__dot" aria-hidden="true"></span>
      <span class="brand__name">BrightNestMums</span>
    </div>
  </section>

  <section class="card card--back" aria-label="Card back">
    <div class="brand brand--back">
      <span class="brand__dot" aria-hidden="true"></span>
      <span class="brand__name">BrightNestMums</span>
    </div>
    <p class="strapline">Tap; Gather; Sorted</p>
  </section>
</main>
</body>
</html>
```